Business Card Design Project

use presentation folder design and my logo and make 4 over 4 business cards

Industry/Entity Type

Business

Requirements
Must have
• use the design from my presentation folder and put my logo on it

Name
Title
phone
fax
email

```html
<!DOCTYPE html>
<html lang="en">
<head>
<meta charset="utf-8">
<title>Kindwell Counseling – Business Card</title>
<link rel="stylesheet" href="https://fonts.googleapis.com/css2?family=Quicksand:wght@500;600&family=Lora:wght@500&display=swap">
<style>
  :root {
    --page: #ecebea;
    --slate: #8c8784;
    --sand: #dcc7b7;
    --sand-light: #e8d9cd;
    --sand-pale: #f0e5dc;
    --ink: #4b4442;
    --brown: #9a6a45;
    --white: #ffffff;
  }
  * { margin: 0; padding: 0; box-sizing: border-box; }
  html, body { width: 1200px; height: 1000px; overflow: hidden; }
  body {
    background: var(--page);
    font-family: "Quicksand", sans-serif;
    display: flex;
    align-items: center;
    justify-content: center;
    gap: 60px;
  }
  .card {
    position: relative;
    width: 525px;
    height: 300px;
    overflow: hidden;
    box-shadow: 0 10px 30px rgba(0,0,0,0.15);
  }
  .card__bg { position: absolute; inset: 0; width: 100%; height: 100%; }

  /* Front */
  .card--front { background: var(--slate); }
  .front-brand {
    position: absolute;
    left: 150px;
    top: 120px;
    display: flex;
    align-items: center;
    gap: 10px;
    color: var(--white);
    font-family: "Lora", serif;
    font-weight: 500;
    font-size: 30px;
  }
  .brand-dot {
    width: 18px; height: 18px; border-radius: 50%;
    background: currentColor;
  }

  /* Back */
  .card--back { background: var(--sand-light); }
  .back-brand {
    position: absolute;
    right: 28px;
    top: 28px;
    display: flex;
    align-items: center;
    gap: 8px;
    color: var(--brown);
    font-family: "Lora", serif;
    font-weight: 500;
    font-size: 22px;
  }
  .back-brand .brand-dot { width: 13px; height: 13px; }
  .person {
    position: absolute;
    left: 165px;
    top: 108px;
  }
  .person__name {
    font-size: 31px;
    font-weight: 600;
    color: var(--ink);
    letter-spacing: 0.5px;
    line-height: 1;
  }
  .person__title {
    font-size: 17px;
    font-weight: 500;
    color: var(--brown);
    margin-left: 38px;
    margin-top: 2px;
  }
  .contact {
    position: absolute;
    left: 30px;
    bottom: 22px;
    list-style: none;
    font-size: 14px;
    font-weight: 500;
    color: var(--ink);
    line-height: 1.3;
  }
  .contact__label { color: var(--brown); font-weight: 600; margin-right: 4px; }
</style>
</head>
<body>

  <section class="card card--front" aria-label="Card front">
    <svg class="card__bg" viewBox="0 0 525 300" preserveAspectRatio="none" aria-hidden="true">
      <polygon points="370,0 525,0 525,300 275,300" fill="var(--sand)"/>
    </svg>
    <div class="front-brand"><span class="brand-dot"></span>Kindwell Counseling</div>
  </section>

  <section class="card card--back" aria-label="Card back">
    <svg class="card__bg" viewBox="0 0 525 300" preserveAspectRatio="none" aria-hidden="true">
      <defs>
        <linearGradient id="sheen" x1="0" y1="0" x2="1" y2="1">
          <stop offset="0" stop-color="var(--sand-pale)"/>
          <stop offset="1" stop-color="var(--sand-light)"/>
        </linearGradient>
      </defs>
      <path d="M230,0 C330,90 440,170 525,210 L525,0 Z" fill="url(#sheen)"/>
    </svg>
    <div class="back-brand"><span class="brand-dot"></span>Kindwell Counseling</div>
    <div class="person">
      <p class="person__name">Daria Kovalen</p>
      <p class="person__title">marketing manager</p>
    </div>
    <ul class="contact">
      <li><span class="contact__label">[P]</span>+11 555 0142</li>
      <li><span class="contact__label">[F]</span>+11 555 0187</li>
      <li><span class="contact__label">[E]</span>hello@kindwell.example</li>
    </ul>
  </section>

</body>
</html>
```